Business Card Design for Marketing Firm

Looking for business card design for higher end marketing firm. Clean but impressionable/trendy. We are a marketing firm that represents manufacturers in the foodservice equipment and supply industry. Our customers are end users such has hotels, restaurants, country clubs, convention centers and casinos as well as distributors of restaurants supplies and equipment, and manufacturers of foodservice equipment and supplies.
Target Market(s)
Hotels, Restaurants, Supply & Equipment Distributors, Foodservice Manufacturers
Industry/Entity Type
Foodservice/Hospitality
Contact Information for Business Card
Name, Title, Contact Number, Email, Website, Social Media, Address
Requirements
Must have
- Clean & Simple but Serious and Impressionable

```html
<!DOCTYPE html>
<html lang="en">
<head>
<meta charset="utf-8">
<title>Meridian Service Reps – Business Card</title>
<link rel="stylesheet" href="https://fonts.googleapis.com/css2?family=Cinzel:wght@600;700&family=Tinos&display=swap">
<style>
  :root {
    --navy: #2a2a78;
    --silver: #bdbdbd;
    --white: #ffffff;
    --stage: #4d4034;
  }
  * { box-sizing: border-box; margin: 0; padding: 0; }
  html, body { width: 901px; height: 1200px; overflow: hidden; }
  body {
    background: var(--stage);
    position: relative;
    font-family: "Tinos", "Times New Roman", serif;
  }
  .card {
    position: absolute;
    left: 87px;
    width: 727px;
    height: 422px;
    border-radius: 24px;
    overflow: hidden;
    box-shadow: 0 8px 16px rgba(0,0,0,0.45);
  }
  .card--front { top: 143px; background: var(--white); }
  .card--back { top: 630px; height: 418px; background: var(--navy); }

  .wave { position: absolute; inset: 0; width: 100%; height: 100%; }

  .brand {
    position: absolute;
    text-align: center;
    font-family: "Cinzel", "Times New Roman", serif;
    font-weight: 700;
  }
  .brand__dot { display: block; margin: 0 auto; border-radius: 50%; }
  .brand__name { display: block; line-height: 1.15; letter-spacing: 0.5px; }

  .card--front .brand { left: 40px; top: 52px; width: 300px; color: var(--navy); }
  .card--front .brand__dot { width: 56px; height: 56px; background: var(--navy); margin-bottom: 16px; }
  .card--front .brand__name { font-size: 23px; }

  .card--back .brand { left: 0; right: 0; top: 92px; color: var(--white); }
  .card--back .brand__dot { width: 92px; height: 92px; background: var(--white); margin-bottom: 28px; }
  .card--back .brand__name { font-size: 40px; }

  .contact {
    position: absolute;
    right: 27px;
    top: 166px;
    text-align: right;
    color: var(--white);
  }
  .contact__name {
    font-family: "Cinzel", "Times New Roman", serif;
    font-weight: 700;
    font-size: 23px;
    letter-spacing: 0.5px;
    line-height: 1;
  }
  .contact__title { font-size: 17px; margin-top: 8px; }
  .contact__address { font-size: 17px; line-height: 26px; margin-top: 9px; }
  .contact__list { list-style: none; margin-top: 8px; }
  .contact__item {
    display: flex;
    justify-content: flex-end;
    align-items: center;
    gap: 10px;
    font-size: 17px;
    height: 26.5px;
  }
  .icon { width: 18px; height: 18px; fill: var(--white); flex: none; }
  .icon--social { width: 16px; height: 16px; border-radius: 50%; background: var(--white); margin-left: 3px; }
</style>
</head>
<body>

<section class="card card--front" aria-label="Card front">
  <svg class="wave" viewBox="0 0 727 422" preserveAspectRatio="none" aria-hidden="true">
    <path fill="var(--navy)" d="M0,289 C150,330 290,285 410,205 C520,132 620,78 727,72 L727,422 L0,422 Z"/>
    <path fill="var(--white)" d="M0,311 C150,352 295,295 415,212 C522,138 622,82 727,77 L727,422 L0,422 Z"/>
    <path fill="var(--silver)" d="M0,317 C150,358 298,300 418,216 C522,142 622,87 727,82 L727,422 L0,422 Z"/>
    <path fill="var(--white)" d="M0,354 C160,392 310,320 430,240 C530,170 620,122 727,115 L727,422 L0,422 Z"/>
    <path fill="var(--navy)" d="M0,359 C160,397 314,324 434,244 C534,174 622,127 727,118 L727,422 L0,422 Z"/>
  </svg>

  <div class="brand">
    <span class="brand__dot"></span>
    <span class="brand__name">Meridian Service<br>Reps</span>
  </div>

  <div class="contact">
    <p class="contact__name">Daniel Marlow</p>
    <p class="contact__title">Co-Founder</p>
    <p class="contact__address">P.O. BOX 42-16 EST-30<br>Linden Ave 14, Fairview</p>
    <ul class="contact__list">
      <li class="contact__item">555-214-3086
        <svg class="icon" viewBox="0 0 24 24" aria-hidden="true"><path d="M3 9c0-3 4-5 9-5s9 2 9 5v1h-5V8H8v2H3z"/><path d="M6 12h12l2 8H4z"/></svg>
      </li>
      <li class="contact__item">hello@meridianservice.com
        <svg class="icon" viewBox="0 0 24 24" aria-hidden="true"><path d="M2 5h20v14H2z"/><path d="M2 5l10 8 10-8" fill="none" stroke="var(--navy)" stroke-width="2"/></svg>
      </li>
      <li class="contact__item">www.meridianservice.com
        <svg class="icon" viewBox="0 0 24 24" aria-hidden="true"><circle cx="12" cy="12" r="10"/><path d="M2 12h20M12 2c4 4 4 16 0 20M12 2c-4 4-4 16 0 20" fill="none" stroke="var(--navy)" stroke-width="1.5"/></svg>
      </li>
      <li class="contact__item">@meridianservice
        <span class="icon icon--social" aria-hidden="true"></span>
      </li>
    </ul>
  </div>
</section>

<section class="card card--back" aria-label="Card back">
  <div class="brand">
    <span class="brand__dot"></span>
    <span class="brand__name">Meridian Service Reps</span>
  </div>
</section>

</body>
</html>
```